Consulting company requires a logo and business card design

I require a logo/business card design for a new company based in Sexsmith Alberta called TallMarsh Integrity Consulting Ltd. I plan to provide the following services: Construction management/inspection for the oil and gas industry, as well as general consulting for Asset Management, fleet management, etc. Have attached a copy of resume for use as guide for

Target Market(s)

Businesses within the oil and gas production, construction and shipping industry

Industry/Entity Type

Oil And Gas

Contact Information for Business Card

Believe should highlight, services offered, safety, quality,

Logo Text

TallMarsh Integrity Consulting (TMIC) ?

Font styles to use
Script

Requirements
Must have
• Open to all options

```html
<!DOCTYPE html>
<html lang="en">
<head>
<meta charset="utf-8">
<title>TallMarsh Integrity Consulting Ltd — Business Card</title>
<link rel="stylesheet" href="https://fonts.googleapis.com/css2?family=Open+Sans:wght@400;600;700&display=swap">
<style>
  :root {
    --backdrop: #9a9a98;
    --card: #0d0d0e;
    --card-edge: #1b1b1d;
    --brand-blue: #4fc3f0;
    --name-cyan: #4fd0f5;
    --text-light: #e6e6e6;
    --text-muted: #b9b9b9;
    --rule: #2a2a2d;
  }
  * { box-sizing: border-box; margin: 0; padding: 0; }
  html, body { width: 1200px; height: 900px; overflow: hidden; }
  body {
    background: var(--backdrop);
    font-family: "Open Sans", sans-serif;
    display: flex;
    flex-direction: column;
    align-items: center;
    justify-content: center;
    gap: 36px;
  }
  .card {
    position: relative;
    width: 700px;
    height: 400px;
    background: radial-gradient(ellipse at 60% 30%, var(--card-edge), var(--card) 70%);
    box-shadow: 0 6px 18px rgba(0,0,0,0.35);
  }
  .brand {
    display: flex;
    align-items: center;
    gap: 14px;
  }
  .brand-dot {
    width: 38px; height: 38px;
    border-radius: 50%;
    background: var(--brand-blue);
    flex: none;
  }
  .brand-name {
    font-weight: 400;
    color: var(--brand-blue);
    line-height: 1.15;
    letter-spacing: 0.02em;
  }

  /* Front */
  .card-front .brand {
    position: absolute;
    top: 92px; left: 0; right: 0;
    justify-content: center;
  }
  .card-front .brand-name { font-size: 34px; }
  .services {
    position: absolute;
    top: 190px; left: 80px; right: 80px;
    text-align: center;
    color: var(--text-light);
    font-size: 17px;
    line-height: 1.45;
  }

  /* Back */
  .person {
    position: absolute;
    top: 92px; left: 48px;
  }
  .person-name {
    color: var(--name-cyan);
    font-weight: 700;
    font-size: 22px;
  }
  .person-title {
    color: var(--text-light);
    font-size: 16px;
    margin-top: 2px;
  }
  .card-back .brand {
    position: absolute;
    top: 84px; right: 44px;
    width: 330px;
  }
  .card-back .brand-name { font-size: 26px; }
  .divider {
    position: absolute;
    top: 185px; left: 300px; right: 40px;
    height: 1px;
    background: var(--rule);
  }
  .contact {
    position: absolute;
    right: 40px; bottom: 48px;
    list-style: none;
    text-align: right;
  }
  .contact li {
    display: flex;
    justify-content: flex-end;
    align-items: center;
    gap: 12px;
    color: var(--text-light);
    font-size: 18px;
    line-height: 1.42;
  }
  .contact svg { width: 15px; height: 15px; flex: none; }
</style>
</head>
<body>

<section class="card card-front" aria-label="Business card front">
  <div class="brand">
    <span class="brand-dot"></span>
    <span class="brand-name">TallMarsh Integrity Consulting Ltd</span>
  </div>
  <p class="services">We are a construction management/inspection for the oil and gas industry, as well as general consulting for Asset Management, fleet management.</p>
</section>

<section class="card card-back" aria-label="Business card back">
  <div class="person">
    <p class="person-name">Daniel Reeve</p>
    <p class="person-title">Managing Director</p>
  </div>
  <div class="brand">
    <span class="brand-dot"></span>
    <span class="brand-name">TallMarsh Integrity Consulting Ltd</span>
  </div>
  <div class="divider"></div>
  <ul class="contact">
    <li>780.555.0142
      <svg viewBox="0 0 16 16" fill="none" stroke="#4fc3f0" stroke-width="1.5"><rect x="4" y="1" width="8" height="14" rx="1.5"/><line x1="7" y1="12.5" x2="9" y2="12.5"/></svg>
    </li>
    <li>780.555.0187
      <svg viewBox="0 0 16 16" fill="#4fc3f0"><path d="M2 6c0-2 3-3.5 6-3.5S14 4 14 6l-2.5 1-1-2h-5l-1 2z"/><rect x="4" y="8" width="8" height="5" rx="1"/></svg>
    </li>
    <li>info@tallmarshic.ca
      <svg viewBox="0 0 16 16" fill="none" stroke="#4fc3f0" stroke-width="1.5"><rect x="1.5" y="3.5" width="13" height="9" fill="#4fc3f0"/><path d="M1.5 3.5 8 9l6.5-5.5" stroke="#0d0d0e"/></svg>
    </li>
    <li>www.tallmarshic.ca
      <svg viewBox="0 0 16 16" fill="none" stroke="#4fc3f0" stroke-width="1.6"><path d="M7 9.5 9.5 7M6 7.5 4 9.5a2.2 2.2 0 0 0 3 3l2-2M10 8.5l2-2a2.2 2.2 0 0 0-3-3l-2 2"/></svg>
    </li>
  </ul>
</section>

</body>
</html>
```